Copper Ridge Inquiries Letterhead

I would like to design a letterhead for a private investigation company. Our primary clients will be law firms. The business card is included below

```html
<!DOCTYPE html>
<html lang="en">
<head>
<meta charset="utf-8">
<title>Copper Ridge Inquiries Letterhead</title>
<link href="https://fonts.googleapis.com/css2?family=Montserrat:wght@400;500;600;700&family=Open+Sans:wght@600&display=swap" rel="stylesheet">
<style>
  :root {
    --navy: #1c3461;
    --orange: #ef5b2f;
    --ink: #555555;
    --body: #9a9a9a;
    --rule: #cfcfcf;
    --backdrop: #ebecef;
    --paper: #ffffff;
  }
  * { margin: 0; padding: 0; box-sizing: border-box; }
  html, body {
    width: 999px; height: 1200px; overflow: hidden;
    background: var(--backdrop);
    font-family: "Montserrat", sans-serif;
  }
  .letterhead {
    position: absolute; left: 84px; top: 17px;
    width: 831px; height: 1166px;
    background: var(--paper);
    overflow: hidden;
  }
  .brand {
    position: absolute; left: 58px; top: 62px; width: 170px;
    text-align: center;
  }
  .brand-dot {
    width: 62px; height: 62px; border-radius: 50%;
    background: var(--orange); margin: 0 auto 12px;
  }
  .brand-name {
    color: var(--navy); font-weight: 700; font-size: 17px;
    line-height: 1.15; letter-spacing: 0.2px;
  }
  .contact {
    position: absolute; right: 78px; top: 82px;
    list-style: none; text-align: right;
  }
  .contact li {
    display: flex; justify-content: flex-end; align-items: center;
    height: 16px; margin-bottom: 9.2px;
    color: var(--navy); font-size: 11px; font-weight: 600; letter-spacing: 0.1px;
  }
  .contact svg { margin-left: 5px; flex: none; }
  .divider {
    position: absolute; left: 59px; top: 226px; width: 710px;
    height: 1px; background: var(--rule);
  }
  .recipient { position: absolute; left: 58px; top: 308px; color: var(--ink); }
  .recipient-name {
    color: var(--orange); font-size: 26px; font-weight: 600;
    letter-spacing: 0.3px; margin-bottom: 14px;
  }
  .recipient p { font-size: 15px; line-height: 22px; margin-bottom: 15px; }
  .letter-date {
    position: absolute; right: 58px; top: 484px;
    font-family: "Open Sans", sans-serif; font-weight: 600;
    font-size: 19px; color: var(--ink);
  }
  .letter-body {
    position: absolute; left: 58px; top: 531px; width: 715px;
    color: var(--body); font-size: 16px; line-height: 25.8px;
    text-align: justify;
  }
  .letter-body p + p { margin-top: 25.8px; }
  .signature {
    position: absolute; left: 620px; top: 910px; width: 118px; height: 73px;
    background: linear-gradient(90deg, #f4f5f8, #eceef3);
    border-radius: 4px;
  }
  .signatory {
    position: absolute; right: 58px; top: 993px;
    color: var(--navy); font-size: 26px; font-weight: 700;
  }
  .footer-band { position: absolute; left: 0; top: 1126px; }
</style>
</head>
<body>
<main class="letterhead">
  <header>
    <div class="brand">
      <div class="brand-dot"></div>
      <div class="brand-name">Copper Ridge Inquiries</div>
    </div>
    <ul class="contact">
      <li>512.404.2319
        <svg width="14" height="14" viewBox="0 0 14 14"><circle cx="7" cy="7" r="7" fill="#ef5b2f"/><path d="M4.4 3.6l1.5-.3.8 1.9-.9.7a5 5 0 0 0 2.3 2.3l.7-.9 1.9.8-.3 1.5c-3.6.2-6.2-2.4-6-6z" fill="#fff"/></svg>
      </li>
      <li>RIVERBEND, TX
        <svg width="14" height="14" viewBox="0 0 14 14"><circle cx="7" cy="7" r="7" fill="#ef5b2f"/><path d="M7 3a2.6 2.6 0 0 0-2.6 2.6C4.4 7.6 7 11 7 11s2.6-3.4 2.6-5.4A2.6 2.6 0 0 0 7 3z" fill="#fff"/><circle cx="7" cy="5.6" r="1" fill="#ef5b2f"/></svg>
      </li>
      <li>LICENSE NO. 04421736
        <svg width="14" height="14" viewBox="0 0 14 14"><circle cx="7" cy="7" r="7" fill="#ef5b2f"/><circle cx="7" cy="5.2" r="1.8" fill="#fff"/><path d="M3.8 10.4a3.2 3.2 0 0 1 6.4 0z" fill="#fff"/></svg>
      </li>
      <li>DANA@COPPERRIDGEINQUIRIES.COM
        <svg width="14" height="14" viewBox="0 0 14 14"><circle cx="7" cy="7" r="7" fill="#ef5b2f"/><text x="7" y="10" text-anchor="middle" font-family="Montserrat, sans-serif" font-size="9" font-weight="700" fill="#fff">@</text></svg>
      </li>
    </ul>
    <div class="divider"></div>
  </header>

  <section class="recipient">
    <h2 class="recipient-name">MORGAN HALE</h2>
    <p>0987-654-321</p>
    <p>info@youremailaddress.com</p>
    <p>4410 Harbor View Rd. Suite<br>210 Lakeview, TX 0000</p>
  </section>

  <time class="letter-date">12 December, 2024</time>

  <article class="letter-body">
    <p>Lorem ipsum dolor sit amet, consectetuer adipiscing elit, sed diam nonummy nibh euismod tincidunt ut laoreet dolore magna aliquam erat volutpat. Ut wisi enim ad minim veniam, quis nostrud exerci tation ullamcorper suscipit lobortis nisl ut aliquip ex ea commodo consequat. Duis autem vel eum iriure dolor in hendrerit in vulputate velit esse molestie consequat, vel illum dolore eu feugiat nulla facilisis at vero eros et accumsan et iusto odio dignissim qui blandit praesent luptatum zzril delenit augue duis dolore te feugait nulla facilisi.</p>
    <p>Lorem ipsum dolor sit amet, cons ectetuer adipiscing elit, sed diam nonummy nibh euismod tincidunt ut laoreet dolore magna aliquam erat volutpat. Ut wisi enim ad minim veniam, quis nostrud exerci tation ullamcorper suscipit lobortis nisl ut aliquip ex ea commodo consequat.</p>
  </article>

  <div class="signature" role="img" aria-label="Handwritten signature of Morgan Hale"></div>
  <p class="signatory">Mr. Morgan Hale</p>

  <svg class="footer-band" width="831" height="40" viewBox="0 0 831 40" aria-hidden="true">
    <polygon points="0,19 688,19 681,27 0,27" fill="#ef5b2f"/>
    <polygon points="706,2 831,2 831,40 0,40 0,32 676,32" fill="#1c3461"/>
  </svg>
</main>
</body>
</html>
```